Tall Fern Roofing Business Card

Need a business card with the logo that was designed here

Contact Information for Business Card

Name, Title, Phone, Email, Website, Company name

```html
<!DOCTYPE html>
<html lang="en">
<head>
<meta charset="utf-8">
<title>Tall Fern Roofing – Business Card</title>
<link href="https://fonts.googleapis.com/css2?family=Open+Sans:wght@400;600;700&display=swap" rel="stylesheet">
<style>
  :root {
    --stage: #e9eaec;
    --brand-blue: #1577c4;
    --brand-blue-deep: #0f5fa3;
    --charcoal: #222226;
    --paper: #ffffff;
    --slate: #9a9ca1;
    --ink-light: #f2f2f2;
  }
  * { margin: 0; padding: 0; box-sizing: border-box; }
  html, body { width: 1200px; height: 780px; overflow: hidden; }
  body {
    background: var(--stage);
    font-family: "Open Sans", Arial, sans-serif;
    display: flex;
    align-items: center;
    justify-content: center;
    gap: 36px;
  }
  .card {
    position: relative;
    width: 560px;
    height: 320px;
    overflow: hidden;
    box-shadow: 0 10px 28px rgba(0,0,0,0.18);
  }

  /* Back side */
  .card-back { background: var(--brand-blue); }
  .card-back .pattern-area {
    position: absolute; inset: 0;
    background: linear-gradient(200deg, #2a8fd6 0%, #1a80cc 30%, #1577c4 60%, #126db6 100%);
  }
  .card-back .brand-name {
    position: absolute;
    right: 40px; top: 222px;
    color: var(--paper);
    font-weight: 600;
    font-size: 20px;
    letter-spacing: 0.4px;
  }

  /* Front side */
  .card-front { background: var(--charcoal); }
  .card-front .curve { position: absolute; inset: 0; }
  .card-front .brand-name {
    position: absolute;
    left: 360px; top: 112px;
    width: 180px;
    text-align: center;
    color: var(--brand-blue);
    font-weight: 600;
    font-size: 21px;
    line-height: 1.2;
  }
  .identity {
    position: absolute;
    left: 0; top: 36px;
    padding-left: 30px;
    border-left: 12px solid var(--brand-blue);
  }
  .identity .name {
    font-size: 29px;
    font-weight: 700;
    line-height: 1.05;
    letter-spacing: 0.4px;
    white-space: nowrap;
  }
  .identity .first { color: var(--brand-blue); }
  .identity .last { color: var(--slate); }
  .identity .title {
    margin-top: 4px;
    color: var(--ink-light);
    font-size: 13px;
    font-weight: 600;
    letter-spacing: 0.3px;
  }
  .contact {
    position: absolute;
    left: 44px; top: 188px;
    color: var(--ink-light);
    font-size: 13px;
    line-height: 1.5;
    list-style: none;
  }
  .contact .address { margin-bottom: 4px; padding-left: 22px; }
  .contact li { display: flex; align-items: center; gap: 8px; white-space: nowrap; }
  .contact svg { width: 14px; height: 14px; flex: none; fill: var(--brand-blue); }
</style>
</head>
<body>

  <section class="card card-back" aria-label="Card back">
    <div class="pattern-area" role="img" aria-label="Repeating pattern of small roofline house outlines in shades of blue"></div>
    <p class="brand-name">Tall Fern Roofing</p>
  </section>

  <section class="card card-front" aria-label="Card front">
    <svg class="curve" viewBox="0 0 560 320" preserveAspectRatio="none" aria-hidden="true">
      <path d="M362 0 C310 70 292 150 330 220 C352 262 380 300 400 320 L560 320 L560 0 Z" fill="var(--brand-blue)"/>
      <path d="M378 0 C326 72 314 150 348 214 C370 256 396 292 418 320 L560 320 L560 0 Z" fill="var(--paper)"/>
    </svg>
    <p class="brand-name">Tall Fern Roofing</p>

    <div class="identity">
      <p class="name"><span class="first">Owen</span> <span class="last">Maddox</span></p>
      <p class="title">Managing Director</p>
    </div>

    <ul class="contact">
      <li class="address">1840 Cedar Ridge Ln. Suite 110<br>Millbrook, TX 75010</li>
      <li>
        <svg viewBox="0 0 24 24" aria-hidden="true"><path d="M6.6 10.8a15.1 15.1 0 0 0 6.6 6.6l2.2-2.2a1 1 0 0 1 1-.25 11.4 11.4 0 0 0 3.6.57 1 1 0 0 1 1 1V20a1 1 0 0 1-1 1A17 17 0 0 1 3 4a1 1 0 0 1 1-1h3.5a1 1 0 0 1 1 1c0 1.25.2 2.45.57 3.57a1 1 0 0 1-.25 1z"/></svg>
        (555) 214-6630
      </li>
      <li>
        <svg viewBox="0 0 24 24" aria-hidden="true"><path d="M3 5h18a1 1 0 0 1 1 1v12a1 1 0 0 1-1 1H3a1 1 0 0 1-1-1V6a1 1 0 0 1 1-1zm1 2.2V17h16V7.2l-8 5.3z"/></svg>
        info@tallfernroofing.com
      </li>
      <li>
        <svg viewBox="0 0 24 24" aria-hidden="true"><circle cx="12" cy="12" r="10"/></svg>
        www.tallfernroofing.com
      </li>
    </ul>
  </section>

</body>
</html>
```